Business cards for 3 Realtors at one brokerage

We will need a business card template that can be projected on 3 business cards. Harborline Realty & Holdings Co. has 3 realtors on staff Dane, Owen, and Miles. We all want a business card that shows our new logo and information. I will attach many versions of our Logo as well as head shots for each realtor (Owen- Long hair, youngest. Miles- Suit jacket, parted hair cut. Dane- Angled Pose, Shirt and Tie.) I have attached our information below.

Dane Foskett
801-555-0147
dane@harborlinehomesite.com
Principal Broker

Miles Tandrow
801-555-0162
miles@harborlinehomesite.com
Real Estate Agent

Owen Tandrow
801-555-0138
owen@harborlinehomesite.com
Real Estate Agent

Harborline Realty & Holdings Co.
HarborlineHomesite.com
5286 N 7200 Suite 208-617, Cedar Bend, UT 84791

Please feel free to reach out with any questions, comments, or concerns.

```html
<!DOCTYPE html>
<html lang="en">
<head>
<meta charset="utf-8">
<title>Harborline Realty – Business Cards</title>
<link href="https://fonts.googleapis.com/css2?family=Montserrat:wght@400;500;600;700&display=swap" rel="stylesheet">
<style>
  :root {
    --page-bg: #e9eaec;
    --card-dark: #4a4a4c;
    --brand-blue: #2f9fea;
    --brand-blue-light: #5cb6f0;
    --text-light: #ffffff;
    --text-silver: #e4e6ea;
    --photo-tone-a: #d8d4cf;
    --photo-tone-b: #8f8a86;
  }
  * { box-sizing: border-box; margin: 0; padding: 0; }
  html, body { width: 1200px; height: 874px; overflow: hidden; }
  body {
    background: var(--page-bg);
    font-family: "Montserrat", sans-serif;
    display: flex;
    align-items: center;
    justify-content: center;
    gap: 70px;
  }
  .card {
    border-radius: 22px;
    position: relative;
    overflow: hidden;
    box-shadow: 0 10px 30px rgba(0,0,0,0.18);
  }

  /* Front */
  .card-front {
    width: 600px;
    height: 343px;
    background: var(--card-dark);
    display: flex;
    flex-direction: column;
    align-items: center;
    justify-content: center;
    gap: 22px;
  }
  .brand-ring {
    width: 112px;
    height: 112px;
    border: 8px solid var(--brand-blue);
    border-radius: 50%;
  }
  .brand-name {
    color: var(--text-silver);
    font-weight: 600;
    text-transform: uppercase;
    text-align: center;
    line-height: 1.35;
  }
  .brand-name .line-main { display: block; font-size: 38px; letter-spacing: 2px; }
  .brand-name .line-sub { display: block; font-size: 15px; letter-spacing: 5px; }

  /* Back */
  .card-back {
    width: 343px;
    height: 600px;
    background: var(--brand-blue);
    color: var(--text-light);
    padding: 56px 36px 40px 46px;
  }
  .back-ring {
    position: absolute;
    width: 470px;
    height: 470px;
    left: -30px;
    top: 120px;
    border: 34px solid var(--brand-blue-light);
    border-radius: 50%;
    opacity: 0.45;
  }
  .back-content { position: relative; }
  .agent-photo {
    width: 158px;
    height: 158px;
    border-radius: 50%;
    background: radial-gradient(circle at 45% 40%, var(--photo-tone-a), var(--photo-tone-b));
    border: 6px solid #f4f4f4;
    margin: 0 auto 28px;
  }
  .agent-name {
    font-size: 23px;
    font-weight: 700;
    text-transform: uppercase;
    letter-spacing: 0.5px;
  }
  .agent-title { font-size: 15px; font-weight: 500; margin-top: 2px; }
  .divider {
    width: 28px;
    height: 3px;
    background: var(--text-light);
    margin: 18px 0 16px;
  }
  .office { font-size: 14px; line-height: 1.45; white-space: nowrap; }
  .contact-icons { display: flex; gap: 8px; margin: 18px 0 12px; }
  .contact-icons svg { width: 22px; height: 22px; }
  .contact-list { font-size: 14px; line-height: 1.5; white-space: nowrap; }
</style>
</head>
<body>
  <section class="card card-front">
    <div class="brand-ring"></div>
    <h1 class="brand-name">
      <span class="line-main">Harborline Realty</span>
      <span class="line-sub">&amp; Holdings Co.</span>
    </h1>
  </section>

  <section class="card card-back">
    <div class="back-ring"></div>
    <div class="back-content">
      <div class="agent-photo" role="img" aria-label="Headshot of agent Miles Tandrow"></div>
      <h2 class="agent-name">Miles Tandrow</h2>
      <p class="agent-title">Real Estate Agent</p>
      <div class="divider"></div>
      <p class="office">
        Harborline Realty &amp; Holdings Co.<br>
        5286 N 7200 Suite 208-617<br>
        Cedar Bend, UT 84791
      </p>
      <div class="contact-icons">
        <svg viewBox="0 0 24 24" aria-hidden="true"><circle cx="12" cy="12" r="12" fill="#fff"/><path d="M8.5 6.5l2 2-1.2 1.6c.8 1.7 2 2.9 3.6 3.6l1.6-1.2 2 2-1.3 1.8c-4 -.3-7.6-3.9-8-8z" fill="#2f9fea"/></svg>
        <svg viewBox="0 0 24 24" aria-hidden="true"><circle cx="12" cy="12" r="12" fill="#fff"/><rect x="6.5" y="8" width="11" height="8" rx="1" fill="#2f9fea"/><path d="M6.8 8.4l5.2 4 5.2-4" stroke="#fff" stroke-width="1.2" fill="none"/></svg>
        <svg viewBox="0 0 24 24" aria-hidden="true"><circle cx="12" cy="12" r="12" fill="#fff"/><circle cx="12" cy="12" r="5.5" fill="none" stroke="#2f9fea" stroke-width="1.5"/><path d="M6.5 12h11M12 6.5c-2.5 3-2.5 8 0 11M12 6.5c2.5 3 2.5 8 0 11" stroke="#2f9fea" stroke-width="1.2" fill="none"/></svg>
      </div>
      <p class="contact-list">
        801-555-0162<br>
        miles@harborlinehomesite.com<br>
        HarborlineHomesite.com
      </p>
    </div>
  </section>
</body>
</html>
```